Flyer for tutoring

The text should be presented in an engaging way to attract potential customers.
Colorfully designed
Around the edge, various objects related to school and the subjects (see text) should be visible.

```html
<!DOCTYPE html>
<html lang="de">
<head>
<meta charset="utf-8">
<title>Nachhilfe Flyer</title>
<link rel="stylesheet" href="https://fonts.googleapis.com/css2?family=Bebas+Neue&family=Montserrat:wght@400;600;700;800&display=swap">
<style>
  :root{
    --yellow:#fde800;
    --purple:#6a2e8c;
    --purple-soft:#7b4aa3;
    --red:#e3000f;
    --sky:#5bc3e6;
    --white:#ffffff;
    --ink:#1d1d1b;
  }
  *{margin:0;padding:0;box-sizing:border-box}
  html,body{width:726px;height:1200px;overflow:hidden;background:#e5e5e5}
  .flyer{position:relative;width:726px;height:1200px;background:var(--yellow);overflow:hidden;font-family:"Montserrat",sans-serif;color:var(--ink)}
  .shapes{position:absolute;inset:0}
  .headline{position:absolute;left:56px;top:58px;width:620px;transform:rotate(-3.5deg);transform-origin:left top}
  .headline__intro{color:var(--white);font-weight:800;font-size:24px;line-height:1.12}
  .headline__accent{color:var(--yellow);font-weight:800;font-size:39px;line-height:1;margin-top:14px}
  .headline__title{color:var(--white);font-family:"Bebas Neue",sans-serif;font-size:78px;line-height:.9;letter-spacing:.5px}
  .cta{position:absolute;left:117px;top:514px;width:493px;height:45px;background:var(--white);color:var(--purple);font-weight:600;font-size:21px;display:flex;align-items:center;justify-content:center}
  .lesson{position:absolute;left:52px;top:592px;width:600px}
  .lesson__title{font-family:"Bebas Neue",sans-serif;color:var(--purple);font-size:31px;line-height:1;letter-spacing:-.2px}
  .lesson__text{font-size:13.4px;line-height:1.25;margin-top:10px;width:590px}
  .promise{position:absolute;left:52px;top:716px;width:560px;height:64px;padding:6px 10px;background:linear-gradient(90deg,var(--purple) 0%,#8d5b8f 45%,rgba(253,232,0,0) 100%);color:var(--white);font-weight:600;font-size:17px;line-height:1.15}
  .motivation{position:absolute;left:56px;top:796px;color:var(--purple);font-weight:800;font-size:26px;line-height:1.05}
  .photo{position:absolute;left:378px;top:818px;width:348px;height:323px}
  .about{position:absolute;left:57px;top:895px;width:296px;padding-left:9px;border-left:1.5px solid var(--ink);font-size:12.4px;line-height:1.2}
  .about strong{font-weight:700}
  .contact{position:absolute;left:55px;top:1026px}
  .contact__title{color:var(--red);font-weight:700;font-size:20px}
  .contact__line{display:flex;align-items:center;gap:3px;margin-top:4px}
  .contact__mail{font-size:21px}
  .contact__phone{color:var(--red);font-weight:800;font-size:22px}
  .contact__note{font-size:10px;margin-left:4px;align-self:flex-end;margin-bottom:4px}
  .icon{width:20px;height:20px;flex:none}
  .footer{position:absolute;left:0;bottom:0;width:726px;height:59px;background:var(--white);font-size:21px;display:flex;align-items:center;justify-content:center}
</style>
</head>
<body>
<main class="flyer">
  <svg class="shapes" width="726" height="1200" viewBox="0 0 726 1200" aria-hidden="true">
    <path d="M0 0H665L697 342Q699 382 670 386L472 402L512 496L378 428L40 480Q8 486 6 456L0 360Z" fill="var(--white)" transform="translate(0 5)"/>
    <path d="M0 0H665L697 342Q699 382 670 386L472 402L512 496L378 428L40 480Q8 486 6 456L0 360Z" fill="var(--purple)"/>
    <path d="M412 342Q470 375 440 445T389 500" fill="none" stroke="var(--white)" stroke-width="3.5"/>
    <path d="M376 512L383 480L402 494Z" fill="var(--white)"/>
    <path d="M653 425H726V543L622 578Z" fill="var(--red)"/>
    <path d="M0 755L43 796L2 863Z" fill="var(--sky)"/>
    <path d="M726 850V1141H640Z" fill="var(--purple-soft)"/>
  </svg>

  <header class="headline">
    <p class="headline__intro">Möchtest du dich gerne in der Schule<br>verbessern undsuchst eine</p>
    <p class="headline__accent">PROFESSIONELLE</p>
    <h1 class="headline__title">NACHHILFELEHRERIN /<br>LERNCOACH ?</h1>
  </header>

  <p class="cta">Dann lass es uns doch mal versuchen!</p>

  <section class="lesson">
    <h2 class="lesson__title">DIE ERSTE LEKTION – DIE KENNENLERNLEKTION – DAUERT CA. 30 MINUTEN.</h2>
    <p class="lesson__text">Sie ist kostenlos. Denn wir müssen ja sicher gehen, dass wir uns verstehen und leiden können. Bei unserem ersten Treffen legen wir auch fest, woran wir arbeiten werden und wann die Nachhilfe in deine Agenda passt.</p>
  </section>

  <p class="promise">Wenn der erste Eindruck stimmt, dann legen wir los,<br>und bald schon werden</p>
  <p class="motivation">deine Motivation und<br>deine Noten besser und besser!</p>

  <div class="photo" role="img" aria-label="Foto: drei fröhliche Schüler mit Schulheften, Daumen hoch" style="background:linear-gradient(160deg,#c9a07e 0%,#8e6f9c 45%,#b2494a 75%,#e9d84a 100%);clip-path:polygon(30% 8%,70% 0,96% 15%,100% 100%,8% 100%,0 55%)"></div>

  <p class="about"><strong>Zu meiner Person:</strong> Ich wohne hier in der Siedlung Lindenweg und bin ausgebildete und sehr erfahrene Sekundar- und Primarlehrerin in den Fächern Deutsch, Französisch, Englisch und Geschichte. (Auf Wunsch auch Mathe-Nachhilfe möglich.)</p>

  <section class="contact">
    <h3 class="contact__title">Meine Kontaktdaten:</h3>
    <p class="contact__line contact__mail">
      <svg class="icon" viewBox="0 0 20 20" aria-hidden="true"><circle cx="10" cy="10" r="9" fill="none" stroke="var(--ink)" stroke-width="1.5"/><rect x="5" y="6.5" width="10" height="7" fill="var(--ink)"/><path d="M5 6.5L10 11L15 6.5" fill="none" stroke="var(--yellow)" stroke-width="1"/></svg>lena.brunner@mailpost.ch
    </p>
    <p class="contact__line">
      <svg class="icon" viewBox="0 0 20 20" aria-hidden="true"><circle cx="10" cy="10" r="9" fill="none" stroke="var(--ink)" stroke-width="1.5"/><path d="M6.5 5.5l2 0 1 2.5-1.3 1a6 6 0 0 0 2.8 2.8l1-1.3 2.5 1v2q-4 1-7-2.5t-1-5.5z" fill="var(--ink)"/></svg><span class="contact__phone">079 412 58 07</span><span class="contact__note">(nachmittags fast immer erreichbar)</span>
    </p>
  </section>

  <footer class="footer">Ich freue mich auf deine Kontaktaufnahme! Bis bald!</footer>
</main>
</body>
</html>
```